Overnight youth camp for refugee kids needs a brochure in Arabic

We need a 3-fold "Z" brochure for an overnight youth camp for Arabic speaking teens in Canada from the Middle East and Africa. The camp's name is Camp Wrenfell. Design should have an outdoors, sports theme and be attractive to teens and their parents. We will supply pictures and text in English. All but the Camp Wrenfell name should be in Arabic.

```html
<!DOCTYPE html>
<html lang="ar">
<head>
<meta charset="utf-8">
<title>Camp Wrenfell – Brochure</title>
<link rel="stylesheet" href="https://fonts.googleapis.com/css2?family=Cairo:wght@600;700;800&family=Lalezar&display=swap">
<style>
:root{
  --green:#72c043;
  --green-dark:#4f9a2a;
  --ink:#1c1c1c;
  --dark:#222427;
  --paper:#ffffff;
  --stage:#ececec;
  --muted:#2b2b2b;
  --photo-warm:#c79a72;
  --photo-sky:#6f9cc4;
  --photo-grass:#6f8f4a;
}
*{box-sizing:border-box;margin:0;padding:0}
html,body{width:781px;height:1200px;overflow:hidden}
body{background:var(--stage);font-family:"Cairo",sans-serif;color:var(--ink);position:relative}
.sheet{position:absolute;left:44px;width:693px;height:537px;background:var(--paper);box-shadow:0 3px 10px rgba(0,0,0,.35);overflow:hidden}
.sheet--outside{top:36px}
.sheet--inside{top:611px}
.panel{position:absolute;top:0;width:231px;height:520px;overflow:hidden}
.panel--left{left:0}
.panel--mid{left:231px}
.panel--right{left:462px}
.abs{position:absolute}
.photo{position:absolute;display:block}
.body-text{direction:rtl;text-align:right;font-weight:700;font-size:7.4px;line-height:1.5}
.on-dark{color:#fff}
.accent{color:var(--green)}
.heading{direction:rtl;text-align:right;font-weight:800;font-size:10px;line-height:1.35}
.checklist{list-style:none;direction:rtl}
.checklist li{display:flex;align-items:flex-start;gap:4px;font-weight:700;font-size:7.2px;line-height:1.35;margin-bottom:3.5px}
.checklist svg{flex:0 0 8px;width:8px;height:8px;margin-top:1px}
.brand-badge{position:absolute;border-radius:50%;background:#fff;border:4px solid var(--dark);display:flex;align-items:center;justify-content:center;box-shadow:0 0 0 2px var(--green)}
.brand-name{font-family:"Cairo",sans-serif;font-weight:800;color:var(--green);line-height:1;text-align:center;direction:ltr}
.footer-bar{position:absolute;left:0;bottom:0;width:693px;height:17px;background:var(--ink);display:flex}
.footer-bar span{flex:1;text-align:center;color:#fff;font-weight:700;font-size:8px;line-height:17px;direction:ltr}
.footer-bar b{color:var(--green);font-weight:700}
.web-pill{position:absolute;height:18px;border-radius:9px;background:var(--green);color:#fff;font-weight:800;font-size:9px;display:flex;align-items:center;justify-content:center;gap:5px;direction:ltr}
.web-pill svg{width:9px;height:9px}
.register{direction:rtl;text-align:right;color:#fff;font-weight:700;font-size:7px;line-height:1.45}
.register .accent{font-size:9px}
.contact{direction:ltr;color:#fff;font-size:6.2px;font-weight:600;display:flex;align-items:center;gap:6px;line-height:1.2}
.contact svg{width:7px;height:7px;flex:0 0 7px}
.title-script{font-family:"Lalezar",sans-serif;color:#fff;direction:rtl;text-align:center;-webkit-text-stroke:1.5px var(--ink);paint-order:stroke fill}
.age{direction:rtl;text-align:center;font-weight:800;font-size:17px}
.goals li{display:flex;gap:4px;direction:rtl;font-weight:700;font-size:7px;line-height:1.5;padding:6px 0;border-bottom:1px solid #d9d9d9}
.goals li:last-child{border-bottom:none}
.goals{list-style:none}
.goals svg{flex:0 0 8px;width:8px;height:8px;margin-top:2px}
.circle-photo{position:absolute;border-radius:50%;border:4px solid var(--green)}
</style>
</head>
<body>

<!-- ===== Outside sheet ===== -->
<section class="sheet sheet--outside">

  <!-- Left panel -->
  <div class="panel panel--left">
    <svg class="photo" style="left:0;top:0" width="231" height="215" viewBox="0 0 231 215" role="img" aria-label="Photo of kids in life jackets on a boat">
      <defs><linearGradient id="boat" x1="0" y1="0" x2="1" y2="1"><stop offset="0" stop-color="#8fb0c9"/><stop offset="1" stop-color="#d5b57c"/></linearGradient></defs>
      <path d="M0 0H231V205C160 178 80 156 0 150Z" fill="url(#boat)"/>
      <path d="M0 150C80 156 160 178 231 205" stroke="var(--green)" stroke-width="5" fill="none"/>
    </svg>
    <div class="circle-photo" style="left:12px;top:158px;width:110px;height:110px;background:var(--photo-sky)" role="img" aria-label="Photo of children swimming in the lake"></div>

    <p class="body-text abs" style="right:12px;top:273px;width:205px">القيم الصحيحة هي اساس فعالياتنا ومغامراتنا كل يوم في هذا المخيم. نحن حريصين على تزويد كل المشتركين بالذكريات بهذا المخيم والتعاليم التي لن ينسوها طوال حياتهم بالاضافة الى الصداقات التي سوف تبدا هنا وستستمر معهم حتى بعد مغادرتهم المخيم.</p>
    <h3 class="heading abs" style="right:12px;top:331px;width:210px;font-size:9px">برنامجنا يتضمن كل من <span class="accent">الفعاليات</span> الاتية :</h3>
    <ul class="checklist abs" style="right:14px;top:352px;width:205px">
      <li><svg viewBox="0 0 10 10"><circle cx="5" cy="5" r="4.3" fill="none" stroke="var(--green)" stroke-width="1"/><path d="M3 5.2l1.4 1.4L7.2 3.8" fill="none" stroke="var(--green)" stroke-width="1.2"/></svg>السباحة</li>
      <li><svg viewBox="0 0 10 10"><circle cx="5" cy="5" r="4.3" fill="none" stroke="var(--green)" stroke-width="1"/><path d="M3 5.2l1.4 1.4L7.2 3.8" fill="none" stroke="var(--green)" stroke-width="1.2"/></svg>العاب الميدان</li>
      <li><svg viewBox="0 0 10 10"><circle cx="5" cy="5" r="4.3" fill="none" stroke="var(--green)" stroke-width="1"/><path d="M3 5.2l1.4 1.4L7.2 3.8" fill="none" stroke="var(--green)" stroke-width="1.2"/></svg>الحرف الفنية</li>
      <li><svg viewBox="0 0 10 10"><circle cx="5" cy="5" r="4.3" fill="none" stroke="var(--green)" stroke-width="1"/><path d="M3 5.2l1.4 1.4L7.2 3.8" fill="none" stroke="var(--green)" stroke-width="1.2"/></svg>القوارب والتجديف</li>
      <li><svg viewBox="0 0 10 10"><circle cx="5" cy="5" r="4.3" fill="none" stroke="var(--green)" stroke-width="1"/><path d="M3 5.2l1.4 1.4L7.2 3.8" fill="none" stroke="var(--green)" stroke-width="1.2"/></svg>التسلق</li>
      <li><svg viewBox="0 0 10 10"><circle cx="5" cy="5" r="4.3" fill="none" stroke="var(--green)" stroke-width="1"/><path d="M3 5.2l1.4 1.4L7.2 3.8" fill="none" stroke="var(--green)" stroke-width="1.2"/></svg>التجمع حول شعلة النار ليلا</li>
      <li><svg viewBox="0 0 10 10"><circle cx="5" cy="5" r="4.3" fill="none" stroke="var(--green)" stroke-width="1"/><path d="M3 5.2l1.4 1.4L7.2 3.8" fill="none" stroke="var(--green)" stroke-width="1.2"/></svg>مغامرات المشي في الطبيعة والهواء الطلق</li>
    </ul>
    <svg class="abs" style="left:0;top:430px" width="231" height="90" viewBox="0 0 231 90">
      <path d="M0 30C70 10 150 40 231 70V90H0Z" fill="var(--dark)"/>
      <path d="M0 24C70 4 150 34 231 64" stroke="var(--green)" stroke-width="3" fill="none"/>
    </svg>
    <div class="brand-name abs" style="left:14px;top:472px;font-size:19px;color:var(--green)">Camp Wrenfell</div>
  </div>

  <!-- Middle panel -->
  <div class="panel panel--mid" style="background:linear-gradient(180deg,#34393b 0%,#1f2224 60%,#17191a 100%)" role="img" aria-label="Dimmed photo of a camp cabin behind the text">
    <div class="brand-badge" style="left:62px;top:28px;width:106px;height:106px">
      <span class="brand-name" style="font-size:14px">Camp<br>Wrenfell</span>
    </div>
    <p class="body-text on-dark abs" style="right:12px;top:148px;width:205px;font-size:7.8px">المخيم يقع بالقرب من مدينة ترينتون، اونتاريو على بعد ساعتين من مدينة تورنتو و ساعات من مدينة اوتاوا و ساعات من مدينة لندن.</p>
    <p class="body-text on-dark abs" style="right:12px;top:226px;width:205px;font-size:7.8px">نحن حريصين على توفير كابينات نوم نظيفة ومريحة ، قاعة طعام جديدة، صالة العاب رياضية، ملاعب رياضية، و ساحل مشرف على البحيرة الخاصة بالمخيم.</p>
    <div class="circle-photo" style="left:58px;top:292px;width:116px;height:116px;background:linear-gradient(135deg,#eef0ec,#d7dcd6)" role="img" aria-label="Street map showing the camp location"></div>
    <p class="register abs" style="right:12px;top:412px;width:210px">للراغبين في التسجيل في المخيم من الفترة <span class="accent">23-28</span> يوليو ، يرجى زيارتنا على الموقع الالكتروني الاتي :</p>
    <div class="web-pill" style="left:28px;top:442px;width:180px">
      <svg viewBox="0 0 10 10"><circle cx="5" cy="5" r="4.3" fill="none" stroke="#fff" stroke-width="1"/><path d="M.7 5h8.6M5 .7c-2 2.4-2 6.2 0 8.6M5 .7c2 2.4 2 6.2 0 8.6" fill="none" stroke="#fff" stroke-width=".8"/></svg>
      www.campwrenfell.ca
    </div>
    <div class="abs" style="left:28px;top:470px;display:flex;flex-direction:column;gap:5px">
      <div class="contact"><svg viewBox="0 0 10 10"><path d="M5 9.5S1.8 6 1.8 3.9a3.2 3.2 0 0 1 6.4 0C8.2 6 5 9.5 5 9.5z" fill="#fff"/><circle cx="5" cy="3.9" r="1.2" fill="var(--dark)"/></svg>48 Birchlane Drive Ottawa,<br>Ontario K2J 0A0</div>
      <div class="contact"><svg viewBox="0 0 10 10"><rect x=".8" y="2" width="8.4" height="6" fill="#fff"/><path d="M.8 2L5 5.4 9.2 2" fill="none" stroke="var(--dark)" stroke-width=".8"/></svg>info@campwrenfell.ca</div>
      <div class="contact"><svg viewBox="0 0 10 10"><path d="M2.2 1l1.8 2-1 1.2c.6 1.3 1.5 2.2 2.8 2.8l1.2-1 2 1.8-1 1.7C4.6 9.2.8 5.4.5 2z" fill="#fff"/></svg>(613) 555-0142</div>
    </div>
  </div>

  <!-- Right panel -->
  <div class="panel panel--right">
    <div class="brand-badge" style="left:105px;top:4px;width:112px;height:112px">
      <span class="brand-name" style="font-size:15px">Camp<br>Wrenfell</span>
    </div>
    <svg class="abs" style="left:0;top:0" width="231" height="150" viewBox="0 0 231 150">
      <path d="M0 0H28C55 80 130 118 231 124V140C130 140 50 118 0 92Z" fill="var(--dark)"/>
      <path d="M0 100C50 126 130 146 231 146" stroke="var(--green)" stroke-width="3" fill="none"/>
    </svg>
    <svg class="photo" style="left:0;top:138px" width="231" height="262" viewBox="0 0 231 262" role="img" aria-label="Photo of cheering campers and counsellors outdoors">
      <defs><linearGradient id="cheer" x1="0" y1="0" x2="0" y2="1"><stop offset="0" stop-color="#7f9a5c"/><stop offset=".6" stop-color="#5a79b0"/><stop offset="1" stop-color="#c9a07a"/></linearGradient></defs>
      <path d="M0 10C80 14 160 12 231 8V262H0Z" fill="url(#cheer)"/>
    </svg>
    <div class="title-script abs" style="left:0;top:188px;width:231px;font-size:24px">مرحبا بفصل</div>
    <div class="title-script abs" style="left:0;top:318px;width:231px;font-size:36px">الصيف الرائع</div>
    <svg class="abs" style="left:0;top:378px" width="231" height="30" viewBox="0 0 231 30">
      <path d="M0 22C80 6 160 6 231 14V30H0Z" fill="#fff"/>
      <path d="M40 18C100 6 170 6 231 12" stroke="var(--green)" stroke-width="4" fill="none"/>
    </svg>
    <p class="body-text abs" style="right:12px;top:404px;width:208px;font-size:8.2px;text-align:center">مغامرات ترفيهية في الهواء الطلق والطبيعة الخلابة تتضمن السباحة و قوارب التجديف وماغيرها من فعاليات اخرى مخيم صيفي للاولاد والبنات للاعمار</p>
    <div class="age abs" style="left:0;top:466px;width:231px">سنوات <span class="accent">9</span> الى <span class="accent">16</span> سنة</div>
  </div>

  <div class="footer-bar">
    <span>www.camp<b>wrenfell</b>.ca</span>
    <span>www.camp<b>wrenfell</b>.ca</span>
    <span>www.camp<b>wrenfell</b>.ca</span>
  </div>
</section>

<!-- ===== Inside sheet ===== -->
<section class="sheet sheet--inside">

  <!-- Middle panel dark base -->
  <div class="panel panel--mid" style="background:linear-gradient(180deg,#2b2f31,#17191a)" role="img" aria-label="Dimmed photo of camp grounds behind the text">
    <div class="brand-badge" style="left:62px;top:150px;width:106px;height:106px">
      <span class="brand-name" style="font-size:14px">Camp<br>Wrenfell</span>
    </div>
    <p class="body-text on-dark abs" style="right:10px;top:262px;width:211px;font-size:7.9px;line-height:1.5">مخيم مع المبيت لمدة خمسة ليالي خصص للشباب من دول شمال افريقيا والشرق الاوسط. الهدف الرئيسي من من المخيم هو التركيز على تطوير الشباب و تحفيزهم على ان يكونوا قادة المستقبل عن طريق ادخال تعاليم الله في حياة المشتركين. املنا هو ان يغادر كل مشترك او مشتركة هذا المخيم مع ذكريات رائعة سوف يتذكرونها طوال حياتهم والمزيد من الثقة بالنفس والتأكيد على قيمة الذات و احترام اكبر للاخرين وانفسهم و مخلوقات الله وقدرة اكبر على اقامة صداقات جديدة والحفاظ عليها وفهم اعمق لوجود الله في حياتهم.</p>
    <p class="register abs" style="right:12px;top:450px;width:210px">للراغبين في التسجيل في المخيم من الفترة <span class="accent">23-28</span> يوليو ، يرجى زيارتنا على الموقع الالكتروني الاتي :</p>
    <div class="web-pill" style="left:28px;top:478px;width:180px">
      <svg viewBox="0 0 10 10"><circle cx="5" cy="5" r="4.3" fill="none" stroke="#fff" stroke-width="1"/><path d="M.7 5h8.6M5 .7c-2 2.4-2 6.2 0 8.6M5 .7c2 2.4 2 6.2 0 8.6" fill="none" stroke="#fff" stroke-width=".8"/></svg>
      www.campwrenfell.ca
    </div>
  </div>

  <!-- Group meal photo across left and middle -->
  <svg class="photo" style="left:0;top:0" width="462" height="195" viewBox="0 0 462 195" role="img" aria-label="Photo of campers sharing a meal at round tables">
    <defs><linearGradient id="meal" x1="0" y1="0" x2="1" y2="1"><stop offset="0" stop-color="#c9b49a"/><stop offset=".5" stop-color="#8f7462"/><stop offset="1" stop-color="#d8cfc4"/></linearGradient></defs>
    <path d="M0 0H462V150C380 150 320 160 231 170C150 180 60 185 0 190Z" fill="url(#meal)"/>
    <path d="M231 172C320 160 380 150 462 150" stroke="var(--green)" stroke-width="4" fill="none"/>
  </svg>

  <!-- Left panel -->
  <div class="panel panel--left" style="height:520px;top:0;background:transparent">
    <svg class="abs" style="left:0;top:150px" width="231" height="60" viewBox="0 0 231 60">
      <path d="M0 40C80 34 160 22 231 20V60H0Z" fill="#fff"/>
      <path d="M0 40C80 34 160 22 231 20" stroke="var(--green)" stroke-width="4" fill="none"/>
    </svg>
    <div class="circle-photo" style="left:8px;top:112px;width:120px;height:120px;background:linear-gradient(135deg,#6e6e6e,#d9b77a)" role="img" aria-label="Photo of kitchen volunteers with trays of food"></div>
    <div class="circle-photo" style="left:122px;top:114px;width:96px;height:96px;background:linear-gradient(135deg,#b9a38a,#5b5048)" role="img" aria-label="Photo of a cook preparing baked dishes"></div>

    <p class="body-text abs" style="right:12px;top:236px;width:207px">سوف نقوم بتوفير وجبات طعام صحية خالية من لحم الخنزير ومتنوعة، عادة يتم تقديم الحبوب والفطائر والتوست الفرنسي على الفطور، وتقديم السندويشات والحساء مع الفواكه على الغداء، وتقديم المعكرونة والهمبرغر والنقانق على العشاء.</p>
    <h3 class="heading abs" style="right:12px;top:309px;width:210px;font-size:10px">التكلفة: <span class="accent">$100</span> لكل استمارة لكل مشترك<br>و تشمل كل ما يلي :</h3>
    <ul class="checklist abs" style="right:14px;top:350px;width:205px">
      <li><svg viewBox="0 0 10 10"><circle cx="5" cy="5" r="4.3" fill="none" stroke="var(--green)" stroke-width="1"/><path d="M3 5.2l1.4 1.4L7.2 3.8" fill="none" stroke="var(--green)" stroke-width="1.2"/></svg>توفير وجبات الطعام والوجبات الخفيفة</li>
      <li><svg viewBox="0 0 10 10"><circle cx="5" cy="5" r="4.3" fill="none" stroke="var(--green)" stroke-width="1"/><path d="M3 5.2l1.4 1.4L7.2 3.8" fill="none" stroke="var(--green)" stroke-width="1.2"/></svg>طهي الطعام والشواء</li>
      <li><svg viewBox="0 0 10 10"><circle cx="5" cy="5" r="4.3" fill="none" stroke="var(--green)" stroke-width="1"/><path d="M3 5.2l1.4 1.4L7.2 3.8" fill="none" stroke="var(--green)" stroke-width="1.2"/></svg>توفير المعدات الرياضية واستعمال البحيرة</li>
      <li><svg viewBox="0 0 10 10"><circle cx="5" cy="5" r="4.3" fill="none" stroke="var(--green)" stroke-width="1"/><path d="M3 5.2l1.4 1.4L7.2 3.8" fill="none" stroke="var(--green)" stroke-width="1.2"/></svg>توفير اللوازم الحرفية والفنية</li>
      <li><svg viewBox="0 0 10 10"><circle cx="5" cy="5" r="4.3" fill="none" stroke="var(--green)" stroke-width="1"/><path d="M3 5.2l1.4 1.4L7.2 3.8" fill="none" stroke="var(--green)" stroke-width="1.2"/></svg>تزويد كل مشترك بصور المخيم على قرص مضغوط</li>
      <li><svg viewBox="0 0 10 10"><circle cx="5" cy="5" r="4.3" fill="none" stroke="var(--green)" stroke-width="1"/><path d="M3 5.2l1.4 1.4L7.2 3.8" fill="none" stroke="var(--green)" stroke-width="1.2"/></svg>تزويد كل مشترك بصورة جماعية لكل المشتركين</li>
    </ul>
    <svg class="abs" style="left:0;top:438px" width="231" height="82" viewBox="0 0 231 82">
      <path d="M0 28C70 8 150 38 231 62V82H0Z" fill="var(--dark)"/>
      <path d="M0 22C70 2 150 32 231 56" stroke="var(--green)" stroke-width="3" fill="none"/>
    </svg>
    <div class="brand-name abs" style="left:14px;top:476px;font-size:19px;color:var(--green)">Camp Wrenfell</div>
  </div>

  <!-- Right panel -->
  <div class="panel panel--right" style="background:#fff">
    <h3 class="heading abs" style="right:14px;top:14px;width:200px;font-size:11px">نحن ملتزمون لتحقيق الاهداف التالية :</h3>
    <ul class="goals abs" style="right:14px;top:58px;width:205px">
      <li><svg viewBox="0 0 10 10"><circle cx="5" cy="5" r="4.3" fill="none" stroke="var(--green)" stroke-width="1"/><path d="M3 5.2l1.4 1.4L7.2 3.8" fill="none" stroke="var(--green)" stroke-width="1.2"/></svg><span>الحرص على حصول جميع المشتركين في المخيم على الراحة التامة من خلال توفير الاماكن المخصصة للاقامة، واختيار الاشخاص الذين سوف يقيمون معهم في غرفهم، وتوفير البرامج الترفيهية والاشخاص المشرفين عليهم.</span></li>
      <li><svg viewBox="0 0 10 10"><circle cx="5" cy="5" r="4.3" fill="none" stroke="var(--green)" stroke-width="1"/><path d="M3 5.2l1.4 1.4L7.2 3.8" fill="none" stroke="var(--green)" stroke-width="1.2"/></svg><span>الحرص على التواصل مع كل مشترك و مساعدة كل الاولاد والبنات على التواصل فيما بينهم و البيئة المحيطة بهم.</span></li>
      <li><svg viewBox="0 0 10 10"><circle cx="5" cy="5" r="4.3" fill="none" stroke="var(--green)" stroke-width="1"/><path d="M3 5.2l1.4 1.4L7.2 3.8" fill="none" stroke="var(--green)" stroke-width="1.2"/></svg><span>الحرص على ان المشرفين على المخيم ان يكونوا مدركين ان كل مشترك او مشتركة هو الهدف الرئيسي من المخيم وهم يستحقون منا كل الرعاية والعناية والاهتمام اينما كانوا ليلا او نهارا.</span></li>
      <li><svg viewBox="0 0 10 10"><circle cx="5" cy="5" r="4.3" fill="none" stroke="var(--green)" stroke-width="1"/><path d="M3 5.2l1.4 1.4L7.2 3.8" fill="none" stroke="var(--green)" stroke-width="1.2"/></svg><span>الحرص على ان يكون المخيم تجربة ممتعة وخبرة ذات مغزى لكل المشتركين.</span></li>
    </ul>
    <svg class="photo" style="left:0;top:330px" width="231" height="190" viewBox="0 0 231 190" role="img" aria-label="Photo of campers gathered around a campfire on a field">
      <defs><linearGradient id="fire" x1="0" y1="0" x2="0" y2="1"><stop offset="0" stop-color="#9db8d6"/><stop offset=".5" stop-color="#6f8f4a"/><stop offset="1" stop-color="#a69a86"/></linearGradient></defs>
      <path d="M0 22C80 40 160 40 231 30V190H0Z" fill="url(#fire)"/>
      <path d="M0 22C80 40 160 40 231 30" stroke="var(--green)" stroke-width="4" fill="none"/>
    </svg>
    <div class="circle-photo" style="left:18px;top:248px;width:116px;height:116px;background:linear-gradient(135deg,#8fae6a,#c9c2a8)" role="img" aria-label="Photo of a camper practising archery"></div>
  </div>

  <div class="footer-bar">
    <span>www.camp<b>wrenfell</b>.ca</span>
    <span>www.camp<b>wrenfell</b>.ca</span>
    <span>www.camp<b>wrenfell</b>.ca</span>
  </div>
</section>

</body>
</html>
```